all natural handmade soap company looking for unique stand out packaging design for bar soaps

we are looking for a unique and stand out on the shelf package design for our hand made soaps for grocery stores. we have a package soap box (picture included) but we are looking for a TOP-NOTCH, CUSTOM, STAND OUT DESIGN FOR THEM. I am supplying our current packaging design, but we want something more unique and STAND OUT. PICTURES i AM INCLUDING ARE: 1: OUR CURRENT PACKAGE DESIGN
2: OUR LIQUID SOAP LABELS (WHICH WE LOVE) AND WOULD LIKE THE BAR SOAPS TO BE SIMILAR
3: WILL BE IN A WHITE BOX WITH A LARGE CUT OUT IN FRONT (SEE SAMPLE BOX BROWN KRAFT).

Target Market(s)

VARIOUS CUSTOMERS. We sell to bright lantern grocers and various grocery stores

Industry/Entity Type

It Company

Requirements
Must have
• cool, unique look that will stand out from a store shelf
• full color acceptable
• our logo on the round part of the package (front)
• please leave a space for bar codes (usually on bottom of box)
• there is a cut out (front) that is there for people to see, feel and smell the soap
• be creative think outside the box open to fresh new designs
Nice to have
• metallic crescent moon (our logo)
Should not have
• organic cannot appear on the front

```html
<!DOCTYPE html>
<html lang="en">
<head>
<meta charset="utf-8">
<title>Lunaverde Bar Soap Box – Bergamot Grapefruit</title>
<link rel="stylesheet" href="https://fonts.googleapis.com/css2?family=Cinzel:wght@400;700&display=swap">
<style>
  :root {
    --olive: #6b7a1c;
    --olive-dark: #5c6a16;
    --kraft: #ba9a6c;
    --kraft-shadow: rgba(80, 60, 30, 0.45);
    --paper: #ffffff;
    --card-edge: #d8d8d8;
    --ink: #1e1e1e;
    --canvas-bg: #ffffff;
  }
  * { box-sizing: border-box; margin: 0; padding: 0; }
  html, body {
    width: 1200px;
    height: 848px;
    overflow: hidden;
    background: var(--canvas-bg);
  }
  .canvas {
    position: relative;
    width: 1200px;
    height: 848px;
  }
  .box-front {
    position: absolute;
    left: 359px;
    top: 80px;
    width: 473px;
    height: 675px;
    background: var(--paper);
    border: 1px solid var(--card-edge);
  }
  .header-band {
    position: absolute;
    left: 12px;
    top: 13px;
    width: 449px;
    height: 162px;
    background: var(--olive);
    border-radius: 14px;
  }
  .soap-window {
    position: absolute;
    left: 2px;
    top: 183px;
    width: 469px;
    height: 326px;
    background: var(--kraft);
    box-shadow: inset 0 8px 10px -4px var(--kraft-shadow),
                inset 0 -8px 10px -4px var(--kraft-shadow);
  }
  .brand-seal {
    position: absolute;
    left: 80px;
    top: 18px;
    width: 310px;
    height: 310px;
    border-radius: 50%;
    background: var(--paper);
    box-shadow: 0 6px 10px rgba(60, 45, 20, 0.35);
    display: flex;
    align-items: center;
    justify-content: center;
  }
  .brand-seal::before {
    content: "";
    position: absolute;
    inset: 21px;
    border-radius: 50%;
    border: 6px solid var(--olive);
  }
  .brand-name {
    position: relative;
    font-family: "Cinzel", serif;
    font-weight: 400;
    font-size: 29px;
    letter-spacing: 1px;
    color: var(--ink);
  }
  .scent-band {
    position: absolute;
    left: 12px;
    top: 521px;
    width: 449px;
    height: 137px;
    background: var(--olive);
    border-radius: 14px;
  }
  .fruit {
    position: absolute;
    border-radius: 50%;
  }
  .fruit-bergamot {
    left: 22px;
    top: 9px;
    width: 110px;
    height: 124px;
    background: radial-gradient(circle at 45% 40%, #e2ee8a 0%, #a8cc3a 55%, #5f8f1e 100%);
  }
  .fruit-grapefruit {
    left: 304px;
    top: 6px;
    width: 141px;
    height: 130px;
    background: radial-gradient(circle at 45% 45%, #f47a6a 0%, #e8544a 55%, #f0a04a 85%, #d98a2e 100%);
  }
  .scent-name {
    position: absolute;
    left: 0;
    right: 0;
    top: 18px;
    text-align: center;
    font-family: "Cinzel", serif;
    font-weight: 700;
    font-size: 27px;
    line-height: 38px;
    color: var(--paper);
    text-shadow: 0 1px 2px rgba(0,0,0,0.35);
  }
  .net-weight {
    position: absolute;
    left: 0;
    right: 0;
    top: 101px;
    text-align: center;
    font-family: Arial, Helvetica, sans-serif;
    font-size: 16px;
    color: var(--paper);
  }
</style>
</head>
<body>
  <main class="canvas">
    <section class="box-front">
      <div class="header-band"></div>
      <div class="soap-window" aria-label="Cut-out window showing the soap bar"></div>
      <div class="brand-seal">
        <span class="brand-name">LUNAVERDE</span>
      </div>
      <div class="scent-band">
        <div class="fruit fruit-bergamot" role="img" aria-label="Photo of a halved bergamot with leaves"></div>
        <div class="fruit fruit-grapefruit" role="img" aria-label="Photo of a halved pink grapefruit with leaves"></div>
        <h1 class="scent-name">BERGAMOT<br>GRAPEFRUIT</h1>
        <p class="net-weight">4.5OZ(127.5g)</p>
      </div>
    </section>
  </main>
</body>
</html>
```